Priority Goals poster for school year

We are an elementary school and the past two years have had you help us to design a "poster" that illustrates our goal of the coming year. I am attaching our last year's one, along with some photos of our (ver rough) thinking for next years. The priority goal at top remains the same. Can't wait to see your genius ideas! :)

Target Market(s)

Staff of an elementary school and parents to some (informative) extent as well.

Colors
296eb1
6094c6
fbed22
fbee3f

Requirements
Must have
• items from the white board picture we have attached

```html
<!DOCTYPE html>
<html lang="en">
<head>
<meta charset="utf-8">
<title>Priority Goals 2021 - 2022</title>
<link rel="stylesheet" href="https://fonts.googleapis.com/css2?family=Fira+Sans+Condensed:ital,wght@0,400;0,500;0,600;0,700;0,800;1,400;1,500&display=swap">
<style>
  :root {
    --blue: #296eb1;
    --blue-light: #6094c6;
    --navy: #1f3470;
    --navy-text: #23386f;
    --yellow: #fbed22;
    --yellow-soft: #fbee3f;
    --yellow-warm: #f3c83f;
    --paper: #f3f3f4;
    --grey-mid: #d4d5d8;
    --grey-edge: #b3b5ba;
    --stage: #ececec;
    --ink: #2b2b2b;
  }
  * { margin: 0; padding: 0; box-sizing: border-box; }
  html, body {
    width: 1200px; height: 900px; overflow: hidden;
    background: var(--stage);
    font-family: "Fira Sans Condensed", sans-serif;
  }
  .poster {
    position: absolute; left: 292px; top: 15px;
    width: 616px; height: 870px;
    box-shadow: 0 6px 24px rgba(0,0,0,.18);
  }
  .poster svg { display: block; width: 100%; height: 100%; }
  .title-year { fill: var(--navy-text); font-weight: 600; font-size: 35px; }
  .title-goals { fill: var(--blue); font-weight: 600; font-size: 35px; }
  .banner-text { fill: #fff; font-weight: 500; font-size: 19.5px; }
  .school-name { fill: var(--blue-light); font-weight: 700; font-size: 15px; letter-spacing: .5px; }
  .big-title { fill: #fff; font-weight: 700; font-size: 41px; }
  .big-year { fill: #fff; font-weight: 600; font-size: 40px; }
  .ribbon-text { fill: var(--ink); font-style: italic; font-size: 13px; }
  .ribbon-text.large { font-size: 22px; font-style: normal; fill: var(--navy-text); }
  .ribbon-text.mid { font-size: 15px; }
  .foundation { fill: var(--navy-text); font-weight: 800; font-size: 38px; }
  .footer-text { fill: #fff; font-weight: 600; font-size: 13.5px; }
  .ribbon-back { fill: none; stroke: var(--blue); }
  .ribbon-face { fill: none; stroke: url(#ribbonYellow); }
  .icon { fill: none; stroke: #fff; stroke-width: 1.3; }
</style>
</head>
<body>
<main class="poster">
<svg viewBox="0 0 730 1032" xmlns="http://www.w3.org/2000/svg">
  <defs>
    <linearGradient id="bannerBlue" x1="0" x2="1">
      <stop offset="0" stop-color="var(--blue)"/>
      <stop offset="1" stop-color="var(--blue-light)"/>
    </linearGradient>
    <radialGradient id="panelGrey" cx=".5" cy=".45" r=".75">
      <stop offset="0" stop-color="#eeeff0"/>
      <stop offset=".55" stop-color="var(--grey-mid)"/>
      <stop offset="1" stop-color="var(--grey-edge)"/>
    </radialGradient>
    <radialGradient id="circleBlue" cx=".5" cy=".5" r=".5">
      <stop offset="0" stop-color="#4a8bcb"/>
      <stop offset=".8" stop-color="var(--blue)"/>
      <stop offset="1" stop-color="var(--blue)" stop-opacity=".6"/>
    </radialGradient>
    <linearGradient id="ribbonYellow" x1="0" x2="1">
      <stop offset="0" stop-color="var(--yellow)"/>
      <stop offset=".6" stop-color="var(--yellow-warm)"/>
      <stop offset="1" stop-color="var(--yellow-soft)"/>
    </linearGradient>
    <linearGradient id="footerNavy" x1="0" x2="1">
      <stop offset="0" stop-color="var(--navy)"/>
      <stop offset="1" stop-color="#3b5894"/>
    </linearGradient>

    <path id="r1" d="M25 520 Q90 330 285 235"/>
    <path id="r2" d="M95 478 Q200 300 400 250"/>
    <path id="r3" d="M175 452 Q300 320 530 295"/>
    <path id="r4" d="M255 442 Q380 350 640 355"/>
    <path id="r5" d="M340 447 Q500 385 728 432"/>
    <path id="r6" d="M0 628 Q200 680 395 620"/>
    <path id="r7" d="M95 712 Q300 700 482 625"/>
    <path id="r8" d="M205 778 Q420 722 565 608"/>
    <path id="r9" d="M335 822 Q520 732 645 575"/>
    <path id="r10" d="M450 848 Q625 720 722 535"/>
  </defs>

  <!-- header -->
  <rect class="header-bg" x="0" y="0" width="730" height="148" fill="var(--paper)"/>
  <rect class="panel" x="0" y="147" width="730" height="795" fill="url(#panelGrey)"/>

  <text x="40" y="78"><tspan class="title-year">2021 - 2022 </tspan><tspan class="title-goals">PRIORITY GOALS</tspan></text>

  <polygon class="goal-banner" points="0,94 505,94 543,138 505,182 0,182" fill="url(#bannerBlue)"/>
  <text class="banner-text" x="25" y="133">We WILL accelerate the academic &amp; social / emotional</text>
  <text class="banner-text" x="25" y="158">growth of the students we served by :</text>

  <g class="school-mark">
    <circle cx="640" cy="62" r="28" fill="var(--blue-light)"/>
    <text class="school-name" x="640" y="118" text-anchor="middle">CEDAR HOLLOW</text>
    <text class="school-name" x="640" y="135" text-anchor="middle">ELEMENTARY</text>
  </g>

  <!-- centre -->
  <circle cx="357" cy="537" r="210" fill="url(#circleBlue)" role="img" aria-label="Blue painted brushstroke circle behind the heading"/>

  <!-- ribbons: back edges -->
  <g class="ribbon-backs" transform="translate(12 10)">
    <use href="#r1" class="ribbon-back" stroke-width="50"/>
    <use href="#r2" class="ribbon-back" stroke-width="44"/>
    <use href="#r3" class="ribbon-back" stroke-width="44"/>
    <use href="#r4" class="ribbon-back" stroke-width="40"/>
    <use href="#r5" class="ribbon-back" stroke-width="40"/>
  </g>
  <g class="ribbon-backs" transform="translate(-14 10)">
    <use href="#r6" class="ribbon-back" stroke-width="42"/>
    <use href="#r7" class="ribbon-back" stroke-width="44"/>
    <use href="#r8" class="ribbon-back" stroke-width="44"/>
    <use href="#r9" class="ribbon-back" stroke-width="48"/>
    <use href="#r10" class="ribbon-back" stroke-width="46"/>
  </g>

  <!-- ribbons: faces -->
  <g class="ribbon-faces">
    <use href="#r1" class="ribbon-face" stroke-width="46"/>
    <use href="#r2" class="ribbon-face" stroke-width="40"/>
    <use href="#r3" class="ribbon-face" stroke-width="40"/>
    <use href="#r4" class="ribbon-face" stroke-width="36"/>
    <use href="#r5" class="ribbon-face" stroke-width="38"/>
    <use href="#r6" class="ribbon-face" stroke-width="40"/>
    <use href="#r7" class="ribbon-face" stroke-width="42"/>
    <use href="#r8" class="ribbon-face" stroke-width="42"/>
    <use href="#r9" class="ribbon-face" stroke-width="46"/>
    <use href="#r10" class="ribbon-face" stroke-width="44"/>
  </g>

  <g class="ribbon-labels">
    <text class="ribbon-text" dy="5"><textPath href="#r1" startOffset="8">Celebrate &amp; Build on 4 years of Success - Our Promise</textPath></text>
    <text class="ribbon-text" dy="5"><textPath href="#r2" startOffset="10">Know who we are and where we are going;  Voices of All</textPath></text>
    <text class="ribbon-text" dy="5"><textPath href="#r3" startOffset="12">Do what we  ♡ love     Teach kids for proven growth</textPath></text>
    <text class="ribbon-text" dy="5"><textPath href="#r4" startOffset="12">Clear, clarified expectations      permissions / support to act</textPath></text>
    <text class="ribbon-text mid" dy="5"><textPath href="#r5" startOffset="20">Communicate! Be intentional with plans / actions</textPath></text>
    <text class="ribbon-text mid" dy="5"><textPath href="#r6" startOffset="30">Use expertise    Use what we have learned</textPath></text>
    <text class="ribbon-text mid" dy="5"><textPath href="#r7" startOffset="40">New Beginnings ; lots of new experiences ahead</textPath></text>
    <text class="ribbon-text" dy="5"><textPath href="#r8" startOffset="28">SEL / Mental Health for all / Connect / ♡ Smile  Laugh</textPath></text>
    <text class="ribbon-text large" dy="8"><textPath href="#r9" startOffset="40">Partnership big / small</textPath></text>
    <text class="ribbon-text" dy="5"><textPath href="#r10" startOffset="20">Stable / Predictable / Consistent (=Strong)</textPath></text>
  </g>

  <text class="big-title" x="357" y="527" text-anchor="middle">THE BIG PICTURE</text>
  <text class="big-year" x="357" y="576" text-anchor="middle">2021 - 2022</text>

  <!-- foundation line -->
  <text class="foundation" x="33" y="920">FOUNDATIONAL BELIEFS AND PROMISES</text>
  <rect class="accent-rule" x="0" y="941" width="730" height="9" fill="var(--yellow)"/>

  <!-- footer -->
  <rect class="footer" x="0" y="950" width="730" height="82" fill="url(#footerNavy)"/>
  <g class="contact">
    <path class="icon" d="M37 968 a6 6 0 0 1 6 6 c0 5 -6 10 -6 10 s-6 -5 -6 -10 a6 6 0 0 1 6 -6 z"/>
    <circle class="icon" cx="37" cy="974" r="2"/>
    <text class="footer-text" x="54" y="980">1180 Birchwood Ave., Lakeview, WA 98000</text>
    <path class="icon" d="M32 999 c1 -2 3 -3 4 -2 l2 3 c0 1 -1 2 -2 2 c1 2 3 4 5 5 c0 -1 1 -2 2 -2 l3 2 c1 1 0 3 -2 4 c-6 1 -13 -6 -12 -12 z"/>
    <text class="footer-text" x="54" y="1007">555-014-2290</text>
    <circle cx="563" cy="1009" r="7" fill="none" stroke="#fff" stroke-width="1.3"/>
    <text class="footer-text" x="578" y="1014">@cedarhollowlearns</text>
  </g>
</svg>
</main>
</body>
</html>
```